Business Card for a New Zealand IT Startup

I need a business card for VELTA Holdings. We are a young startup based in New Zealand working in internet marketing and web development. The design should have some element connected to New Zealand, such as wave, koru or silver fern, just don't use a kiwi bird.

```html
<!DOCTYPE html>
<html lang="en">
<head>
<meta charset="utf-8">
<title>VELTA Holdings – Business Card</title>
<link rel="stylesheet" href="https://fonts.googleapis.com/css2?family=Roboto:wght@400;500;700&display=swap">
<style>
  :root {
    --page-bg: #d9dcdf;
    --card-bg: #eef1f4;
    --brand-blue: #1f4f9e;
    --band-blue: #1d4a94;
    --band-blue-dark: #163a78;
    --accent-red: #e2452c;
    --text-light: #e4e9f1;
    --text-soft: #c9d2df;
  }
  html, body {
    margin: 0;
    width: 1200px;
    height: 969px;
    overflow: hidden;
    background: var(--page-bg);
    font-family: "Roboto", Arial, sans-serif;
  }
  .business-card {
    position: absolute;
    left: 120px;
    top: 210px;
    width: 960px;
    height: 550px;
    border-radius: 24px;
    background: var(--card-bg);
    overflow: hidden;
    box-shadow: 0 10px 30px rgba(0,0,0,0.15);
  }
  .card-shapes {
    position: absolute;
    inset: 0;
  }
  .brand {
    position: absolute;
    left: 62px;
    top: 92px;
    display: flex;
    align-items: center;
    gap: 18px;
  }
  .brand-dot {
    width: 34px;
    height: 34px;
    border-radius: 50%;
    background: var(--accent-red);
  }
  .brand-name {
    font-weight: 700;
    font-size: 58px;
    color: var(--brand-blue);
    letter-spacing: 1px;
  }
  .contact {
    position: absolute;
    right: 46px;
    top: 268px;
    text-align: right;
    color: var(--text-light);
  }
  .contact-name {
    font-size: 33px;
    font-weight: 500;
    margin: 0;
    letter-spacing: 0.5px;
  }
  .contact-title {
    font-size: 21px;
    margin: 4px 0 26px;
    letter-spacing: 0.5px;
  }
  .contact-address {
    font-size: 20px;
    line-height: 29px;
    color: var(--text-soft);
    margin: 0 0 18px;
  }
  .contact-list {
    list-style: none;
    margin: 0;
    padding: 0;
    font-size: 20px;
    line-height: 31px;
    color: var(--text-soft);
  }
  .contact-list li {
    display: flex;
    justify-content: flex-end;
    align-items: center;
    gap: 12px;
  }
  .contact-list .phone { color: var(--text-light); font-size: 21px; }
  .icon { width: 18px; height: 18px; fill: var(--text-soft); }
</style>
</head>
<body>
  <div class="business-card">
    <svg class="card-shapes" viewBox="0 0 960 550" width="960" height="550" aria-hidden="true">
      <defs>
        <linearGradient id="band-gradient" x1="0" y1="0" x2="1" y2="1">
          <stop offset="0" stop-color="var(--band-blue)"/>
          <stop offset="1" stop-color="var(--band-blue-dark)"/>
        </linearGradient>
      </defs>
      <path class="wave-band" fill="url(#band-gradient)"
            d="M0,428 C100,480 190,518 300,513 C470,505 560,300 700,190 C800,110 900,60 960,30 L960,550 L0,550 Z"/>
      <path class="wave-accent" fill="var(--accent-red)"
            d="M40,432 C120,482 200,510 300,502 C470,492 560,290 700,180 C740,150 770,110 800,78 C775,110 745,155 705,192 C565,305 475,505 300,509 C200,514 120,485 40,432 Z"/>
    </svg>

    <div class="brand">
      <span class="brand-dot"></span>
      <span class="brand-name">VELTA Holdings</span>
    </div>

    <div class="contact">
      <p class="contact-name">MARA QUINLAN</p>
      <p class="contact-title">CEO/FOUNDER</p>
      <p class="contact-address">42 Harbour Crest Road<br>Wellington, NZ 6011</p>
      <ul class="contact-list">
        <li class="phone">021 555 0192
          <svg class="icon" viewBox="0 0 24 24"><path d="M6.6 10.8a15.1 15.1 0 0 0 6.6 6.6l2.2-2.2a1 1 0 0 1 1-.25 11.4 11.4 0 0 0 3.6.57 1 1 0 0 1 1 1V20a1 1 0 0 1-1 1A17 17 0 0 1 3 4a1 1 0 0 1 1-1h3.5a1 1 0 0 1 1 1c0 1.25.2 2.45.57 3.57a1 1 0 0 1-.25 1Z"/></svg>
        </li>
        <li>mara@veltaholdings.com
          <svg class="icon" viewBox="0 0 24 24"><path d="M2 5h20v14H2Z M3.5 6.5 12 13l8.5-6.5" fill="none" stroke="var(--text-soft)" stroke-width="2"/><path d="M2 6l10 7 10-7v13H2Z"/></svg>
        </li>
        <li>www.veltaholdings.com
          <svg class="icon" viewBox="0 0 24 24"><circle cx="12" cy="12" r="9.5" fill="none" stroke="var(--text-soft)" stroke-width="2"/><path d="M2.5 12h19M12 2.5c3 3 3 16 0 19M12 2.5c-3 3-3 16 0 19" fill="none" stroke="var(--text-soft)" stroke-width="1.6"/></svg>
        </li>
      </ul>
    </div>
  </div>
</body>
</html>
```